Redesign of business card for Cedar Ridge Mechanical

We are looking for a new design for our business cards for Cedar Ridge Mechanical. We are a plumbing & HVAC construction company, operating on the West Coast of Canada and USA. Logo attached.
Industry/Entity Type
Construction - Plumbing & HVAC
Contact Information for Business Card
Name, address, phone numbers, email, website address
Look and feel
Each slider illustrates characteristics of the customer's brand and the style your logo design should communicate.

```html
<!DOCTYPE html>
<html lang="en">
<head>
<meta charset="utf-8">
<title>Cedar Ridge Mechanical – Business Card</title>
<link href="https://fonts.googleapis.com/css2?family=Montserrat:wght@400;700&display=swap" rel="stylesheet">
<style>
  :root {
    --backdrop: #6f6f6f;
    --card: #1b1b1b;
    --card-deep: #0e0e0e;
    --silver: #d9d9d9;
    --silver-soft: #a9a9a9;
    --rule: #6a6a6a;
  }
  html, body {
    margin: 0;
    width: 1200px;
    height: 800px;
    overflow: hidden;
    background: var(--backdrop);
    font-family: "Montserrat", sans-serif;
  }
  .stage {
    position: relative;
    width: 1200px;
    height: 800px;
  }
  .card {
    position: absolute;
    top: 245px;
    width: 540px;
    height: 310px;
    border-radius: 18px;
    background: var(--card);
    box-shadow: 0 14px 30px rgba(0,0,0,0.35);
    overflow: hidden;
  }
  .card--front { left: 40px; }
  .card--back { left: 620px; }

  /* Front */
  .brand-block {
    position: absolute;
    left: 0; top: 0;
    width: 250px; height: 310px;
    display: flex;
    align-items: center;
    justify-content: center;
    gap: 12px;
  }
  .brand-square {
    width: 22px; height: 22px;
    background: var(--silver);
    flex: none;
  }
  .brand-name {
    color: var(--silver);
    font-weight: 700;
    font-size: 19px;
    line-height: 1.25;
    letter-spacing: 0.04em;
    text-transform: uppercase;
  }
  .divider {
    position: absolute;
    left: 262px; top: 40px;
    width: 1px; height: 230px;
    background: var(--rule);
  }
  .details {
    position: absolute;
    left: 290px; top: 44px;
    color: var(--silver-soft);
    font-size: 12.5px;
    line-height: 1.5;
  }
  .person-name {
    color: var(--silver);
    font-weight: 700;
    font-size: 19px;
    letter-spacing: 0.03em;
    margin: 0;
  }
  .person-role { margin: 0 0 18px; font-size: 13px; }
  .address { margin: 0 0 18px; }
  .contact-list { list-style: none; margin: 0; padding: 0; }
  .contact-list li { display: flex; align-items: center; gap: 8px; }
  .contact-list svg { width: 11px; height: 11px; fill: var(--silver-soft); flex: none; }

  /* Back */
  .pattern-field {
    position: absolute; inset: 0;
    background: linear-gradient(120deg, var(--card-deep) 0%, #1f1f1f 45%, #3a3a3a 80%, #262626 100%);
  }
  .back-brand {
    position: absolute;
    left: 330px; top: 140px;
    display: flex; align-items: center; gap: 8px;
  }
  .back-brand .brand-square { width: 12px; height: 12px; }
  .back-brand .brand-name { font-size: 11px; }
</style>
</head>
<body>
<div class="stage">
  <section class="card card--front">
    <div class="brand-block">
      <span class="brand-square"></span>
      <span class="brand-name">Cedar Ridge<br>Mechanical</span>
    </div>
    <div class="divider"></div>
    <div class="details">
      <p class="person-name">MARTIN CALDER</p>
      <p class="person-role">President</p>
      <p class="address">4127 Harbor Lane<br>Suite 200, Tustin, CA 92780</p>
      <ul class="contact-list">
        <li><svg viewBox="0 0 16 16"><path d="M3 1l3 3-2 2c1 2 3 4 5 5l2-2 3 3-2 3C6 15 1 10 0 3z"/></svg>1-866-555-0148 Toll Free</li>
        <li><svg viewBox="0 0 16 16"><path d="M3 1l3 3-2 2c1 2 3 4 5 5l2-2 3 3-2 3C6 15 1 10 0 3z"/></svg>213-555-0192</li>
        <li><svg viewBox="0 0 16 16"><path d="M0 3h16v10H0z M1 4l7 5 7-5" fill-rule="evenodd"/></svg>info@cedarridgemech.com</li>
        <li><svg viewBox="0 0 16 16"><circle cx="8" cy="8" r="7"/></svg>www.cedarridgemech.com</li>
      </ul>
    </div>
  </section>

  <section class="card card--back">
    <div class="pattern-field" role="img" aria-label="Repeating brand mark pattern in glossy black and silver"></div>
    <div class="back-brand">
      <span class="brand-square"></span>
      <span class="brand-name">Cedar Ridge Mechanical</span>
    </div>
  </section>
</div>
</body>
</html>
```